4th Generation Family Business Needs a New Card Design!

We are a family owned 4th Generation company. We are based in the Sydney, Australia area and we are desperately in need of a more modern and classy card. We are monumental masons who design, supply & erect lasting memorials throughout cemeteries in Sydney. Our customers are normally in a period of grieving. I have attached logo files that will need to be implemented on the card. Company was established 1935. Australian Owned and Operated. Card needs to be designed to PIXO.com specification.

Target Market(s)

Our target market is based upon people that a grieving for family members that have passed away. We also deal with alot of companies that own and operate cemeteries.

Industry/Entity Type

Business

Contact Information for Business Card

Simon Harcourt, Operations Manager, 0417293086, simon@harcourtmemorials.com.au
Lewis Harcourt, Director, 0491630572, lewis@harcourtmemorials.com.au
Phone # 02 9561 3048
Website: www.harcourtmemorials.com.au
Address: Suite 17, 8 Palfrey Lane, West Carlow, Sydney NSW 2156

Font styles to use
Serif
Decorative
Script

Requirements
Must have
• Would like to see the logo nicely implemented with a modern design. Embossed lettering would be a nice additive.

```html
<!DOCTYPE html>
<html lang="en">
<head>
<meta charset="utf-8">
<title>Harcourt Memorials – Business Card</title>
<link href="https://fonts.googleapis.com/css2?family=Open+Sans:wght@400;700&display=swap" rel="stylesheet">
<style>
  :root {
    --backdrop: #e4e1dc;
    --card: #f7f6f2;
    --ink: #1c1c1c;
    --gold: #e8b923;
    --rule: #2a2a2a;
  }
  * { margin: 0; padding: 0; box-sizing: border-box; }
  html, body { width: 909px; height: 1200px; overflow: hidden; }
  body {
    background: var(--backdrop);
    font-family: "Open Sans", Arial, sans-serif;
    color: var(--ink);
    position: relative;
  }
  .card {
    position: absolute;
    left: 104px;
    width: 700px;
    height: 428px;
    background: var(--card);
    box-shadow: 0 2px 6px rgba(0,0,0,0.18);
  }
  .card--front { top: 120px; }
  .card--back { top: 652px; }

  /* shared brand lockup */
  .brand { display: flex; align-items: center; gap: 12px; }
  .brand__mark { flex: none; background: var(--gold); }
  .brand__name { font-weight: 700; color: var(--ink); white-space: nowrap; }

  /* front */
  .brand--front {
    position: absolute;
    left: 0; right: 0; top: 168px;
    justify-content: center;
  }
  .brand--front .brand__mark { width: 22px; height: 22px; }
  .brand--front .brand__name { font-size: 34px; letter-spacing: 1px; }
  .accent-rule {
    position: absolute;
    left: 220px; width: 260px; top: 230px;
    border-top: 3px solid var(--gold);
  }

  /* back */
  .contact { position: absolute; left: 50px; top: 44px; }
  .contact__name { font-size: 20px; font-weight: 700; text-transform: uppercase; letter-spacing: 0.5px; line-height: 1.1; }
  .contact__role { font-size: 15px; font-weight: 700; margin-bottom: 6px; }
  .contact__line { font-size: 12.5px; line-height: 1.5; }
  .rule-short {
    position: absolute; left: 48px; top: 150px; width: 200px;
    border-top: 1px solid var(--rule);
  }
  .rule-long {
    position: absolute; left: 48px; top: 188px; width: 604px;
    border-top: 1px solid var(--rule);
  }
  .brand--back {
    position: absolute; right: 48px; top: 160px;
    gap: 7px;
  }
  .brand--back .brand__mark { width: 11px; height: 11px; }
  .brand--back .brand__name { font-size: 14px; letter-spacing: 0.5px; }
  .office {
    position: absolute; left: 50px; top: 318px;
    font-size: 12.5px; line-height: 1.5;
  }
  .address {
    position: absolute; right: 50px; top: 350px;
    font-size: 12.5px; line-height: 1.5; text-align: right;
  }
</style>
</head>
<body>
  <section class="card card--front" aria-label="Card front">
    <div class="brand brand--front">
      <span class="brand__mark"></span>
      <span class="brand__name">Harcourt Memorials</span>
    </div>
    <div class="accent-rule"></div>
  </section>

  <section class="card card--back" aria-label="Card back">
    <div class="contact">
      <p class="contact__name">Simon Harcourt</p>
      <p class="contact__role">Operations Manager</p>
      <p class="contact__line">M. 0417293086</p>
      <p class="contact__line">simon@harcourtmemorials.com.au</p>
    </div>
    <div class="rule-short"></div>
    <div class="brand brand--back">
      <span class="brand__mark"></span>
      <span class="brand__name">Harcourt Memorials</span>
    </div>
    <div class="rule-long"></div>
    <div class="office">
      <p>P. 02 9561 3048</p>
      <p>www.harcourtmemorials.com.au</p>
    </div>
    <div class="address">
      <p>Suite 17, 8 Palfrey Lane</p>
      <p>West Carlow, Sydney NSW 2156</p>
    </div>
  </section>
</body>
</html>
```